Modern design company business card design

We are a design oriented construction firm. The owner is an architect and licensed General Contractor and accomplished furniture designer. We do new home construction and large scale remodeling and office design. We would like a design for our new business cards that is clean and modern, but relatable. We like the bright green color of our logo mixed with different shades of grey. We're also open to reinterpreting the logo.

Target Market(s)

Potential design clients,
Construction clients

Industry/Entity Type

Architecture

Contact Information for Business Card

Tall Maple Design | Build Inc. (optional with logo, Inc. optional)Jeffrey MorganOwner (optional)317.555.0148 cell317.431.8056 officejmorgan@greensquareinc.comwww.greensquareinc.com

Font styles to use
Sans Serif
Other font styles liked:
• Avenir

Requirements
Nice to have
• I like designs that have some continuity between the front and back, i.e. similar layouts or graphic elements that wrap around the card. I tend to prefer horizontal over vertical, but that's not a have to. I also tend to prefer white or recycled paper.

```html
<!DOCTYPE html>
<html lang="en">
<head>
<meta charset="utf-8">
<title>Tall Maple Design | Build – Business Card</title>
<link href="https://fonts.googleapis.com/css2?family=Source+Sans+3:wght@400;600&display=swap" rel="stylesheet">
<style>
  :root {
    --backdrop: #1c1c1c;
    --paper: #ffffff;
    --green-light: #c6dd6b;
    --green-mid: #a4d262;
    --green-deep: #72c05a;
    --green-text: #8cc63f;
    --grey-brand: #8c8c8c;
    --ink: #1a1a1a;
    --back-name: #b7df78;
  }
  * { box-sizing: border-box; margin: 0; padding: 0; }
  html, body { width: 1200px; height: 900px; overflow: hidden; }
  body {
    background: var(--backdrop);
    font-family: "Source Sans 3", "Myriad Pro", sans-serif;
    position: relative;
  }
  .card {
    position: absolute;
    top: 170px;
    width: 347px;
    height: 561px;
    overflow: hidden;
  }
  .card--front { left: 259px; background: var(--paper); }
  .card--back {
    left: 631px;
    background: linear-gradient(to bottom, var(--green-light) 0%, var(--green-mid) 55%, var(--green-deep) 100%);
  }
  .band {
    position: absolute;
    left: 102px;
    width: 143px;
    background: linear-gradient(to bottom, var(--green-light), var(--green-deep));
  }
  .band--top { top: 0; height: 30px; }
  .band--bottom { bottom: 0; height: 28px; }

  .brand {
    position: absolute;
    left: 0;
    top: 196px;
    width: 100%;
    text-align: center;
    color: var(--grey-brand);
    font-weight: 400;
    font-size: 24px;
    line-height: 30px;
    letter-spacing: 2px;
    text-transform: uppercase;
  }

  .person {
    position: absolute;
    top: 341px;
    left: 0;
    width: 100%;
    text-align: center;
  }
  .person__name { color: var(--green-text); font-size: 19px; font-weight: 600; line-height: 24px; }
  .person__role { color: var(--ink); font-size: 15px; line-height: 20px; }

  .contacts {
    position: absolute;
    top: 408px;
    left: 0;
    width: 100%;
    list-style: none;
    text-align: center;
    color: var(--ink);
    font-size: 15.5px;
    line-height: 23px;
  }
  .contacts svg { width: 11px; height: 11px; margin-right: 4px; vertical-align: -1px; fill: var(--green-text); }

  .back-name {
    position: absolute;
    top: 50%;
    left: 0;
    width: 100%;
    transform: translateY(-50%);
    text-align: center;
    color: var(--back-name);
    font-size: 46px;
    font-weight: 600;
    letter-spacing: 3px;
    text-transform: uppercase;
    line-height: 52px;
  }
</style>
</head>
<body>
  <section class="card card--front">
    <div class="band band--top"></div>

    <div class="brand">
      <p>Tall Maple</p>
      <p>Design | Build</p>
    </div>

    <div class="person">
      <p class="person__name">Dennis Holloway</p>
      <p class="person__role">Owner</p>
    </div>

    <ul class="contacts">
      <li><svg viewBox="0 0 12 12"><path d="M2.5 0.5l2 2.5-1 1.2c.7 1.5 1.8 2.6 3.3 3.3l1.2-1 2.5 2-1 2c-4.8-.3-8.7-4.2-9-9z"/></svg>317.555.0172</li>
      <li><svg viewBox="0 0 12 12"><path d="M3 0h6a1 1 0 0 1 1 1v10a1 1 0 0 1-1 1H3a1 1 0 0 1-1-1V1a1 1 0 0 1 1-1zm.6 1.5v7.5h4.8V1.5zM6 9.6a.7.7 0 1 0 0 1.4.7.7 0 0 0 0-1.4z"/></svg>317.555.0148</li>
      <li><svg viewBox="0 0 12 12"><path d="M0 2h12v1L6 7 0 3zm0 2.2l6 4 6-4V10H0z"/></svg>dholloway@tallmapleinc.example</li>
      <li><svg viewBox="0 0 12 12"><path d="M5 7l2-2M4.2 5.6L2.6 7.2a1.8 1.8 0 0 0 2.6 2.6l1.6-1.6M7.8 6.4l1.6-1.6a1.8 1.8 0 0 0-2.6-2.6L5.2 3.8" fill="none" stroke="#8cc63f" stroke-width="1.3"/></svg>www.tallmapleinc.example</li>
    </ul>

    <div class="band band--bottom"></div>
  </section>

  <section class="card card--back">
    <p class="back-name">Tall<br>Maple</p>
  </section>
</body>
</html>
```